Birchmoor Kell Executive Development Workshop Series

* Had error in first version of MS Word doc and have re-uploaded - twelve subject areas, not nine *
I'd like a flyer to print to hand out and post on my website birchmoorkell.com to advertise a workshop series I'm launching. I'd like it to build strongly on the wonderful logo you did and Scottish theme...and to have the same "feel" as my website. birchmoorkell.com
It should be 8.5x11, single sided. Not sure if I should use full color glossy or two-color on nice paper. Regardless, I will most likely have it done on a color copier and will not put it on a printing press.
I have typed up a document with all the information in a MS Word file, but need you to lay it out in an aesthetically pleasing way. I have attached that MS Word file.
I am also attaching a handful of similar flyer documents from other non-competing coaches in my network. I think they all have their merits, but leave me under-whelmed.
I'm also attaching a picture of me and some pictures of Scotland my parents took about 10 years ago. I'm reluctantly open to stock photos, just not too obvious or hackneyed (if that word can be applied to pictures as well as expressions).
Lastly, this workshop series will be an ongoing thing, so I'd like to be able to make minor edits myself with things like new dates or topics.
Thank you!
Target Market(s)
Small business owners and emerging leaders with large companies
Colors
Designer to choose colors to be used in the design.
Requirements
Should not have
- Obviously stock photos

```html
<!DOCTYPE html>
<html lang="en">
<head>
<meta charset="utf-8">
<title>Birchmoor Kell Executive Development Workshop Series</title>
<link href="https://fonts.googleapis.com/css2?family=Tinos:wght@400;700&display=swap" rel="stylesheet">
<style>
:root{
  --backdrop:#2b2b2b;
  --paper:#ffffff;
  --header-bg:#eceeea;
  --forest:#3b4a22;
  --forest-text:#2f3a1a;
  --sage:#b7c99a;
  --ink:#1c1c1c;
  --badge:#6b4a70;
}
*{margin:0;padding:0;box-sizing:border-box}
html,body{width:1020px;height:1200px;overflow:hidden;background:var(--backdrop)}
body{position:relative;font-family:'Tinos',serif;color:var(--ink)}
.flyer{position:absolute;left:103px;top:74px;width:815px;height:1052px;background:var(--paper)}
.abs{position:absolute}
.header{left:0;top:0;width:815px;height:103px;background:var(--header-bg)}
.brand{left:30px;top:34px;display:flex;align-items:center;gap:10px}
.brand-dot{width:20px;height:20px;border-radius:50%;background:var(--forest)}
.brand-name{font-size:22px;font-weight:400;color:var(--forest-text)}
.coach-name{left:250px;top:26px;width:300px;text-align:center;font-size:42px;font-weight:400;color:var(--forest-text);line-height:1}
.name-rule{left:250px;top:82px;width:300px;height:2px;background:linear-gradient(90deg,transparent,var(--forest) 30%,var(--forest) 70%,transparent)}
.contact{left:553px;top:16px;list-style:none;font-size:12.5px;line-height:19px}
.contact li{display:flex;align-items:center;gap:10px}
.contact svg{width:13px;height:13px;flex:none}
.intro-title{left:19px;top:448px;font-size:23.5px;font-weight:700;color:var(--forest-text)}
.intro{left:19px;top:484px;width:780px;font-size:11.6px;line-height:13.6px}
.intro p+p{margin-top:13px}
.schedule{left:0;top:581px;width:581px;height:257px;background:var(--forest);color:#fff;padding:10px 70px 0 20px}
.schedule ul{list-style:none;font-size:12px;line-height:13.4px}
.schedule li{position:relative;padding-left:16px}
.schedule li::before{content:"";position:absolute;left:0;top:5px;width:4px;height:4px;border-radius:50%;background:#fff}
.includes-title{left:17px;top:852px;font-size:24px;font-weight:700;color:var(--ink)}
.includes{left:17px;top:884px;width:620px;font-size:11.4px;line-height:12.4px}
.includes strong{color:var(--forest-text)}
.badge{left:668px;top:856px;width:110px;height:150px;border-radius:6px;background:var(--badge)}
.stripe-dark{left:0;top:1042px;width:587px;height:10px;background:var(--forest)}
.stripe-light{left:587px;top:1042px;width:228px;height:10px;background:var(--sage)}
</style>
</head>
<body>
<main class="flyer">
  <header class="abs header"></header>
  <div class="abs brand"><span class="brand-dot"></span><span class="brand-name">Birchmoor Kell</span></div>
  <h1 class="abs coach-name">Alan Dunmore</h1>
  <div class="abs name-rule"></div>
  <ul class="abs contact">
    <li><svg viewBox="0 0 16 16"><circle cx="8" cy="8" r="7.5" fill="none" stroke="#333"/><path d="M5 4.5l1.5-.5 1 2-1 .8a5 5 0 002.2 2.2l.8-1 2 1-.5 1.5C8 11 5 8 5 4.5z" fill="#333"/></svg>(336)555-0148</li>
    <li><svg viewBox="0 0 16 16"><circle cx="8" cy="8" r="7.5" fill="#333"/><rect x="4" y="5.5" width="8" height="5" fill="none" stroke="#fff"/><path d="M4 5.5l4 3 4-3" fill="none" stroke="#fff"/></svg>alan@birchmoorkell.com</li>
    <li><svg viewBox="0 0 16 16"><circle cx="8" cy="8" r="7.5" fill="#333"/><circle cx="8" cy="8" r="3.5" fill="none" stroke="#fff"/><path d="M4.5 8h7M8 4.5v7" stroke="#fff"/></svg>www.birchmoorkell.com</li>
    <li><svg viewBox="0 0 16 16"><circle cx="8" cy="8" r="7.5" fill="#333"/><path d="M8 12s-3-3.2-3-5.2a3 3 0 016 0C11 8.8 8 12 8 12z" fill="#fff"/><circle cx="8" cy="6.8" r="1" fill="#333"/></svg>218 Kiln Street, Greenfield NC 27105</li>
  </ul>

  <div class="abs" role="img" aria-label="Misty Scottish glen with green mountain slopes and a valley road" style="left:0;top:108px;width:581px;height:324px;background:linear-gradient(180deg,#c9ccce 0%,#8f9590 30%,#5d6b4a 60%,#6f7f3e 85%,#8a8a78 100%)"></div>
  <div class="abs" role="img" aria-label="Highland cattle grazing in front of a white-cottage village by a loch" style="left:587px;top:126px;width:228px;height:140px;background:linear-gradient(180deg,#aab7c4 0%,#d8d8d0 35%,#7a8a4e 60%,#8a5a34 85%,#6f8a3e 100%)"></div>
  <div class="abs" role="img" aria-label="Rocky sea shore under a grey sky" style="left:587px;top:274px;width:111px;height:158px;background:linear-gradient(180deg,#c6ccd2 0%,#a7b0b6 40%,#5d6a6e 65%,#3e3a32 100%)"></div>
  <div class="abs" role="img" aria-label="Portrait of the coach in a suit" style="left:706px;top:274px;width:109px;height:158px;background:linear-gradient(180deg,#6c5f57 0%,#7a6b60 50%,#4e463f 100%)"></div>

  <h2 class="abs intro-title">Birchmoor Kell Executive Development Workshop Series – First Thursdays</h2>
  <div class="abs intro">
    <p>A positive, fresh, results-driven approach for businesses to increase profits by building confidence, command and control in owners and executives. We will use proven leadership and business strategies to improve work-life balance, buy-in, and company value. Here's your opportunity to meet with other like-minded business owners and executives once a month in a private and confidential setting.</p>
    <p>We've got twelve subject areas planned, and while they are all powerful, we will shift from high-level strategy topics to “where the rubber meets the road” topics.</p>
  </div>

  <section class="abs schedule">
    <ul>
      <li><b>Sep 7</b> – My Company Owns Me – What a CEO should and should not do</li>
      <li><b>Oct 5</b> – Taking Vision / Mission / Values Down To The Molecular Level Of Your Company</li>
      <li><b>Nov 2</b> – People Problems – The biggest waste of time and money for every small business</li>
      <li><b>Dec 7</b> – Value Delivery Systems – Re-think everything you think you know about creating value</li>
      <li><b>Jan 4, 2018</b> – Rally Your Team Around A Goal – How to create a meaningful company goal and rally the troops around it</li>
      <li><b>Feb 1</b> – Building Your Executive Leadership Team – You can't succeed without one</li>
      <li><b>Mar 1</b> – Improve Your Outside Sales Efforts – Help your sales force to be busy AND successful</li>
      <li><b>Apr 5</b> – Every Brain In The Game – Engage your team and build a strong culture</li>
      <li><b>May 3</b> – Repeatable Processes – Coach your employees how to get predictable results every time</li>
      <li><b>Jun 7</b> – Finding and Filling Profit Holes – Most small businesses waste more money than they profit</li>
      <li><b>*Jul 12</b> – Put Your Payroll On A Diet – Why waste happens, what to do about it and how it helps everyone</li>
      <li><b>Aug 2</b> – Truly, How Effective Are You With This Whole “Leadership” Thing?</li>
    </ul>
  </section>
  <div class="abs" role="img" aria-label="Red-fronted pub with flower baskets and a small dog statue" style="left:587px;top:581px;width:228px;height:257px;background:linear-gradient(180deg,#b9aa94 0%,#a89a86 35%,#b22a22 55%,#8e1f1a 80%,#6d6a64 100%)"></div>

  <h2 class="abs includes-title">Each month of this monthly workshop series includes:</h2>
  <div class="abs includes">
    <strong>3-Hour Intensive Workshop</strong> - High-energy, creative sessions with engaging and relevant business topics, peer group advisory board (master mind), and networking (9am – 12pm, dates above) and<br>
    <strong>90-minute one-on-one coaching session</strong> – to help you absorb and apply the revelations from the group sessions to your own business (mutually scheduled)<br>
    Participation and trust is vital to your investment; no holding back. Due to the confidential nature of the intensive workshops, all participants will sign a confidentiality agreement. Additionally, we will only allow one company per industry to be represented.<br>
    To register, go to birchmoorkell.com/exec-dev and click the registration link<br>
    $395/month or $295/month with a 6-month or greater commitment<br>
    All monthly Intensive Workshops will be 9am – 12pm on the dates above at Foundry Commons Coworking at 218 Kiln Street, Greenfield NC 27105<br>
    All one-on-one coaching sessions will be mutually scheduled with Alan Dunmore once you have registered
  </div>

  <div class="abs badge" role="img" aria-label="Professional coaching association membership badge"></div>

  <div class="abs stripe-dark"></div>
  <div class="abs stripe-light"></div>
</main>
</body>
</html>
```